Business card for Internet Marketing Consultant

Simple - need a nice business card design using the logo elements and colors. Keywords: Progressive, professional, stylish, minimalist. Please use the nb as part of the design.

Info for card:

Brendan Okafor
Internet Marketing Strategist
Phone: (520) 555-0148
Email: brendan@northbeamgrowth.com
Address: 2193 W. Larkmoor Ave., Ste. 118
Tucson, Arizona 85710

Website: www.northbeamgrowth.com

Industry/Entity Type

Business

Font styles to use
Sans Serif

```html
<!DOCTYPE html>
<html lang="en">
<head>
<meta charset="utf-8">
<title>Northbeam Growth – Business Card</title>
<link rel="stylesheet" href="https://fonts.googleapis.com/css2?family=Open+Sans:wght@400;600;700&display=swap">
<style>
  :root {
    --stage: #3a2c23;
    --card: #ffffff;
    --brand-blue: #3b6fb6;
    --brand-green: #6cbd72;
    --green-deep: #5aa862;
    --text-gray: #444a52;
    --label: #ffffff;
  }
  * { margin: 0; padding: 0; box-sizing: border-box; }
  html, body { width: 1200px; height: 782px; overflow: hidden; }
  body {
    background: var(--stage);
    font-family: "Open Sans", Arial, sans-serif;
    position: relative;
  }
  .card {
    position: absolute;
    width: 464px;
    height: 264px;
    background: var(--card);
    overflow: hidden;
  }
  .card--front { left: 364px; top: 80px; }
  .card--back-green { left: 110px; top: 396px; background: var(--brand-green); }
  .card--back-white { left: 630px; top: 397px; }

  .brand {
    position: absolute;
    left: 0; right: 0;
    display: flex;
    flex-direction: column;
    align-items: center;
  }
  .brand__row { display: flex; align-items: center; gap: 8px; }
  .brand__dot {
    width: 26px; height: 26px; border-radius: 50%;
    background: var(--brand-blue);
  }
  .brand__name {
    font-size: 27px; font-weight: 600; color: var(--brand-blue);
    letter-spacing: -0.3px; line-height: 1;
  }
  .brand__tagline {
    margin-top: 4px; margin-left: 34px;
    font-size: 9.5px; letter-spacing: 1.6px; color: var(--brand-blue);
  }
  .card--front .brand { top: 50px; }
  .card--back-white .brand { top: 88px; }

  .person { position: absolute; top: 132px; left: 0; right: 0; text-align: center; }
  .person__name { font-size: 16px; font-weight: 700; color: var(--brand-blue); }
  .person__title { margin-top: 4px; font-size: 11px; color: var(--text-gray); }

  .rule { position: absolute; height: 1px; background: var(--brand-green); }
  .card--front .rule { left: 29px; right: 30px; top: 196px; }
  .card--back-white .rule { left: 29px; right: 30px; top: 224px; }

  .contacts { position: absolute; left: 27px; top: 204px; list-style: none; }
  .contacts li {
    display: flex; align-items: center; gap: 7px;
    height: 16px; font-size: 11px; color: var(--text-gray);
  }
  .contacts svg { width: 10px; height: 10px; fill: var(--brand-blue); }
  .divider {
    position: absolute; left: 232px; top: 214px;
    width: 1px; height: 24px; background: var(--brand-green);
  }
  .address {
    position: absolute; left: 281px; top: 220px;
    font-size: 11px; line-height: 16px; color: var(--text-gray);
  }

  .site {
    position: absolute; font-size: 11.5px; letter-spacing: 2px;
  }
  .card--back-green .site { left: 44px; top: 40px; color: #fff; font-weight: 600; }
  .card--back-white .site { left: 0; right: 0; top: 236px; text-align: center; color: var(--brand-green); }

  .back-accent {
    position: absolute; left: -40px; top: 96px;
    width: 220px; height: 220px; border-radius: 50%;
    background: var(--green-deep);
  }

  .label {
    position: absolute; font-size: 33px; color: var(--label);
  }
  .label--one { left: 112px; top: 682px; }
  .label--two { left: 633px; top: 693px; }
</style>
</head>
<body>

  <section class="card card--front">
    <div class="brand">
      <div class="brand__row">
        <span class="brand__dot"></span>
        <span class="brand__name">northbeamgrowth</span>
      </div>
      <span class="brand__tagline">INTERNET MARKETING STRATEGIES</span>
    </div>

    <div class="person">
      <p class="person__name">Brendan Okafor</p>
      <p class="person__title">Internet Marketing Strategist</p>
    </div>

    <div class="rule"></div>

    <ul class="contacts">
      <li>
        <svg viewBox="0 0 10 10" aria-hidden="true"><path d="M2 0.5 L3.6 0.5 L4.2 3 L3 3.8 Q4 6 6.2 7 L7 5.8 L9.5 6.4 L9.5 8 Q9.5 9.5 8 9.5 Q1 9 0.5 2 Q0.5 0.5 2 0.5Z"/></svg>
        (520) 555-0148
      </li>
      <li>
        <svg viewBox="0 0 10 10" aria-hidden="true"><path d="M0.5 2 H9.5 V8.5 H0.5Z M1.2 2.6 L5 5.6 L8.8 2.6" stroke="#fff" stroke-width="0.8"/></svg>
        brendan@northbeamgrowth.com
      </li>
      <li>
        <svg viewBox="0 0 10 10" aria-hidden="true"><circle cx="5" cy="5" r="4.5"/><path d="M0.5 5 H9.5 M5 0.5 V9.5 M5 0.5 Q2 5 5 9.5 M5 0.5 Q8 5 5 9.5" stroke="#fff" stroke-width="0.6" fill="none"/></svg>
        www.northbeamgrowth.com
      </li>
    </ul>

    <div class="divider"></div>

    <p class="address">2193 W. Larkmoor Ave., Ste.<br>118, Tucson, Arizona 85710</p>
  </section>

  <section class="card card--back-green">
    <div class="back-accent"></div>
    <p class="site">www.northbeamgrowth.com</p>
  </section>

  <section class="card card--back-white">
    <div class="brand">
      <div class="brand__row">
        <span class="brand__dot"></span>
        <span class="brand__name">northbeamgrowth</span>
      </div>
      <span class="brand__tagline">INTERNET MARKETING STRATEGIES</span>
    </div>
    <div class="rule"></div>
    <p class="site">www.northbeamgrowth.com</p>
  </section>

  <p class="label label--one">Back option 1</p>
  <p class="label label--two">Back option 2</p>

</body>
</html>
```